Bramwell Crest Electric van design

Looking to design a wrap for a 2021 varenta cargolux high roof using orange black and dark grey colors like in the logo

```html
<!DOCTYPE html>
<html lang="en">
<head>
<meta charset="utf-8">
<title>Bramwell Crest Electric – Van Wrap</title>
<link rel="stylesheet" href="https://fonts.googleapis.com/css2?family=Montserrat:wght@400;600;700&display=swap">
<style>
  :root {
    --wrap-orange: #e8582c;
    --wrap-black: #1d1d1f;
    --wrap-grey: #4a4c50;
    --wrap-white: #ffffff;
    --page-bg: #eceef0;
    --font-main: "Montserrat", Arial, sans-serif;
  }
  html, body {
    margin: 0;
    padding: 0;
    width: 1200px;
    height: 3436px;
    overflow: hidden;
    background: var(--page-bg);
  }
  .wrap-sheet {
    width: 1200px;
    height: 3436px;
    display: flex;
    flex-direction: column;
  }
  .view { display: block; width: 1200px; }
  .view--side { height: 600px; }
  .view--front { height: 917px; }
  .view--rear { height: 1316px; }
  .brand-name {
    font-family: var(--font-main);
    font-weight: 600;
  }
  .phone, .web {
    font-family: var(--font-main);
    font-weight: 700;
  }
  .fill-orange { fill: var(--wrap-orange); }
  .fill-black { fill: var(--wrap-black); }
  .fill-grey { fill: var(--wrap-grey); }
  .fill-white { fill: var(--wrap-white); }
</style>
</head>
<body>
<main class="wrap-sheet">

  <!-- Driver side panel -->
  <svg class="view view--side" viewBox="0 0 1200 600" aria-label="Side panel, driver side">
    <defs>
      <clipPath id="side-body-left"><rect x="40" y="40" width="1120" height="520" rx="40"/></clipPath>
    </defs>
    <g clip-path="url(#side-body-left)">
      <rect class="fill-white" x="40" y="40" width="1120" height="520"/>
      <path class="fill-orange" d="M210 560 L310 420 Q325 400 360 400 L960 400 L960 460 L385 460 L300 560 Z"/>
      <path class="fill-orange" d="M90 560 L160 470 L200 470 L130 560 Z"/>
      <path class="fill-black" d="M900 40 C820 200 840 420 980 560 L1200 560 L1200 40 Z"/>
      <rect class="fill-grey" x="40" y="510" width="1120" height="50"/>
    </g>
    <circle class="fill-orange" cx="1045" cy="230" r="88"/>
    <text class="brand-name fill-black" x="420" y="205" font-size="42">Bramwell Crest</text>
    <text class="brand-name fill-black" x="420" y="256" font-size="42">Electric</text>
    <text class="phone fill-white" x="480" y="444" font-size="34" letter-spacing="1">555.014.2290</text>
  </svg>

  <!-- Passenger side panel -->
  <svg class="view view--side" viewBox="0 0 1200 600" aria-label="Side panel, passenger side">
    <defs>
      <clipPath id="side-body-right"><rect x="40" y="40" width="1120" height="520" rx="40"/></clipPath>
    </defs>
    <g clip-path="url(#side-body-right)" transform="translate(1200 0) scale(-1 1)">
      <rect class="fill-white" x="40" y="40" width="1120" height="520"/>
      <path class="fill-orange" d="M210 560 L310 420 Q325 400 360 400 L960 400 L960 460 L385 460 L300 560 Z"/>
      <path class="fill-orange" d="M90 560 L160 470 L200 470 L130 560 Z"/>
      <path class="fill-black" d="M900 40 C820 200 840 420 980 560 L1200 560 L1200 40 Z"/>
      <rect class="fill-grey" x="40" y="510" width="1120" height="50"/>
    </g>
    <circle class="fill-orange" cx="155" cy="230" r="88"/>
    <text class="brand-name fill-black" x="400" y="205" font-size="42">Bramwell Crest</text>
    <text class="brand-name fill-black" x="400" y="256" font-size="42">Electric</text>
    <text class="phone fill-white" x="470" y="444" font-size="34" letter-spacing="1">555.014.2290</text>
  </svg>

  <!-- Front hood panel -->
  <svg class="view view--front" viewBox="0 0 1200 917" aria-label="Front hood panel">
    <defs>
      <clipPath id="hood-body"><path d="M180 260 Q600 220 1020 260 L1060 660 Q600 690 140 660 Z"/></clipPath>
    </defs>
    <g clip-path="url(#hood-body)">
      <rect class="fill-white" x="0" y="0" width="1200" height="917"/>
      <path class="fill-black" d="M240 330 Q600 300 960 330 L1000 620 Q600 650 200 620 Z"/>
      <path class="fill-orange" d="M140 300 L240 330 L200 620 L140 640 Z"/>
      <path class="fill-orange" d="M1060 300 L960 330 L1000 620 L1060 640 Z"/>
    </g>
    <circle class="fill-orange" cx="385" cy="475" r="68"/>
    <text class="brand-name fill-white" x="480" y="462" font-size="46">Bramwell Crest</text>
    <text class="brand-name fill-white" x="480" y="516" font-size="46">Electric</text>
  </svg>

  <!-- Rear doors panel -->
  <svg class="view view--rear" viewBox="0 0 1200 1316" aria-label="Rear doors panel">
    <rect class="fill-black" x="170" y="60" width="860" height="1200" rx="60"/>
    <rect class="fill-grey" x="598" y="60" width="4" height="1200"/>
    <circle class="fill-orange" cx="600" cy="275" r="135"/>
    <text class="brand-name fill-white" x="600" y="550" font-size="72" text-anchor="middle">Bramwell Crest</text>
    <text class="brand-name fill-white" x="600" y="638" font-size="72" text-anchor="middle">Electric</text>
    <path class="fill-orange" d="M290 680 L930 670 L910 770 L300 760 Z"/>
    <text class="phone fill-white" x="605" y="744" font-size="62" text-anchor="middle" letter-spacing="2">555.014.2290</text>
    <text class="web fill-white" x="600" y="925" font-size="36" text-anchor="middle">bramwellcrestelectric.com</text>
  </svg>

</main>
</body>
</html>
```